NZ First of it's kind solutions directory and marketplace for busy Mums needs a business card design

We need a business card design for our new nationwide business in NZ (long term plans to go global). We provide solutions to the everyday challenges that busy Mums face by connecting them with quality communities and suppliers of carefully selected, relevant products and services. We sell direct via our online marketplace. The final design should communicate our values of inclusivity, quality and smart solutions. Colours should incorporate our logo colour palette of #477077 and #6ba8b2. Our website is at https://www.brightnestmums.example

Target Market(s)

busy Mums, Age 28 – 50, female, income over $100K, location main centres NZ primarily but NZ wide. Is likely juggling work or career with a young family. Probably had hobbies which have fallen by the wayside.
-Wants to succeed in her chosen career without compromising on family life
-to successfully juggle her career without feeling like she is compromising her children
- Is time poor, something always has to give and it’s generally her health (she’ll stay up late, get stressed)
- probably ex corporate or professional career. Has discretional income

Industry/Entity Type

Business

Contact Information for Business Card

Lena Forbisher, Founder, BrightNestMums.example (Strapline Tap; Gather; Sorted), 47 Kowhai Terrace, Ellerslie, Auckland 1051, New Zealand. Mob: 021 483 517 Ph: +64 (0)9 571 4860

Font styles to use
Other font styles liked:
• Raleway, and/or Architects Daughter

Colors
00a990
33b8a4
86cfc6
cfeae6

Requirements
Must have
• the above details, streamline. the logo and colours associated with those logos
Should not have
• foil or metallic colours

```html
<!DOCTYPE html>
<html lang="en">
<head>
<meta charset="utf-8">
<title>BrightNestMums business card</title>
<link rel="stylesheet" href="https://fonts.googleapis.com/css2?family=Work+Sans:wght@400;500;600&display=swap">
<style>
  :root {
    --teal-dark: #477077;
    --teal-light: #6ba8b2;
    --paper: #ffffff;
    --backdrop: #e0e0e0;
  }
  * { margin: 0; padding: 0; box-sizing: border-box; }
  html, body {
    width: 1200px;
    height: 897px;
    overflow: hidden;
    background: var(--backdrop);
    font-family: "Work Sans", sans-serif;
  }
  .card {
    position: absolute;
    left: 303px;
    width: 595px;
    height: 339px;
  }
  .card--front { top: 92px; background: var(--paper); color: var(--teal-dark); }
  .card--back { top: 469px; background: var(--teal-dark); color: var(--paper); }

  .brand {
    position: absolute;
    left: 0; right: 0;
    display: flex;
    align-items: center;
    justify-content: center;
    gap: 12px;
  }
  .card--front .brand { top: 60px; }
  .card--back .brand { top: 146px; }
  .brand__dot {
    width: 34px; height: 34px;
    border-radius: 50%;
    background: currentColor;
    flex: none;
  }
  .brand__name {
    font-weight: 600;
    font-size: 38px;
    letter-spacing: -0.5px;
    line-height: 48px;
  }

  .person {
    position: absolute;
    top: 164px;
    left: 0; right: 0;
    text-align: center;
  }
  .person__name {
    font-size: 28px;
    font-weight: 500;
    color: var(--teal-light);
    line-height: 34px;
  }
  .person__role {
    font-size: 15px;
    letter-spacing: 0.6px;
    line-height: 18px;
  }
  .person__rule {
    width: 64px;
    height: 1px;
    margin: 12px auto 0;
    background: var(--teal-dark);
  }

  .contact {
    position: absolute;
    top: 243px;
    left: 0; right: 0;
    text-align: center;
    font-size: 14.5px;
    letter-spacing: 0.6px;
    line-height: 23px;
  }
  .contact__label { color: var(--teal-light); }

  .back-url {
    position: absolute;
    top: 297px;
    left: 0; right: 0;
    text-align: center;
    font-size: 14.5px;
    font-weight: 500;
    letter-spacing: 1px;
  }
</style>
</head>
<body>
  <section class="card card--front">
    <div class="brand">
      <span class="brand__dot"></span>
      <span class="brand__name">BrightNestMums</span>
    </div>
    <div class="person">
      <p class="person__name">Lena Forbisher</p>
      <p class="person__role">Founder</p>
      <div class="person__rule"></div>
    </div>
    <div class="contact">
      <p><span class="contact__label">M :</span> 021 483 517 | <span class="contact__label">P :</span> +64 (0)9 571 4860</p>
      <p><span class="contact__label">W :</span> www.brightnestmums.example</p>
      <p><span class="contact__label">A :</span> 47 Kowhai Terrace, Ellerslie Auckland 1051, New Zealand</p>
    </div>
  </section>

  <section class="card card--back">
    <div class="brand">
      <span class="brand__dot"></span>
      <span class="brand__name">BrightNestMums</span>
    </div>
    <p class="back-url">www.brightnestmums.example</p>
  </section>
</body>
</html>
```